Kitchen and custom cabinetry company looking for business card design

We make: * Custom Kitchens, contemporary and traditional kitchens, Vanities, Libraries, Custom Entry Doors, Custom Wine Cellars and Custom Design Furniture. Phone number 555-284-7716. Address: Westhampton NY. Email: KAVRO@mailbox.example Portfolio at: KAVROcabinetry.example I would like moderns fonts and not heavy lines. double side but maybe will use clear plastic. I attached the logo.

Industry/Entity Type

Business

```html
<!DOCTYPE html>
<html lang="en">
<head>
<meta charset="utf-8">
<title>KAVRO Cabinetry Inc. – Business Card</title>
<link rel="stylesheet" href="https://fonts.googleapis.com/css2?family=Poiret+One&display=swap">
<style>
  :root {
    --page-bg: #d8d3cb;
    --orange: #f15d2a;
    --orange-soft: #f5835f;
    --grey: #828282;
    --grey-soft: #b6b6b6;
    --white: #ffffff;
    --logo-grey: #8a8a8a;
    --card-font: "Poiret One", sans-serif;
  }
  * { margin: 0; padding: 0; box-sizing: border-box; }
  html, body {
    width: 1200px;
    height: 970px;
    overflow: hidden;
    background: var(--page-bg);
    font-family: var(--card-font);
  }
  .canvas { position: relative; width: 1200px; height: 970px; }

  .card-side {
    position: absolute;
    top: 151px;
    width: 409px;
    height: 714px;
  }
  .card-side--front { left: 162px; }
  .card-side--back { left: 625px; }

  .top-band {
    position: absolute; left: 0; top: 0; width: 100%; height: 30px;
    border-radius: 23px 23px 0 0;
  }
  .logo-panel {
    position: absolute; left: 0; top: 30px; width: 100%; height: 267px;
    background: var(--white);
    display: flex; flex-direction: column; align-items: center; justify-content: center;
  }
  .accent-strip {
    position: absolute; left: 0; top: 324px; width: 100%; height: 47px;
  }
  .info-panel {
    position: absolute; left: 0; top: 394px; width: 100%; height: 320px;
    border-radius: 0 0 23px 23px;
    color: var(--white);
    text-align: center;
  }

  .card-side--front .top-band,
  .card-side--front .info-panel { background: var(--orange); }
  .card-side--front .accent-strip { background: var(--orange-soft); }
  .card-side--back .top-band,
  .card-side--back .info-panel { background: var(--grey); }
  .card-side--back .accent-strip { background: var(--grey-soft); }

  .brand {
    display: flex; align-items: center; gap: 14px;
    color: var(--logo-grey);
  }
  .brand-mark {
    width: 22px; height: 22px; background: var(--orange);
  }
  .brand-name {
    font-size: 64px; line-height: 1; letter-spacing: 6px;
    font-weight: 400;
  }
  .brand-sub {
    margin-top: 10px;
    font-size: 21px; letter-spacing: 7px;
    color: var(--logo-grey);
  }

  .contact { padding-top: 42px; }
  .contact-name { font-size: 24px; line-height: 1; }
  .contact-role { font-size: 18px; margin-top: 12px; opacity: 0.8; }
  .contact-lines { margin-top: 18px; font-size: 20px; line-height: 31px; }
  .contact-address { margin-top: 10px; font-size: 20px; line-height: 32px; }

  .services {
    list-style: none;
    padding-top: 92px;
    font-size: 19px; line-height: 28.5px; letter-spacing: 0.5px;
  }
</style>
</head>
<body>
<main class="canvas">

  <section class="card-side card-side--front" aria-label="Card front">
    <div class="top-band"></div>
    <div class="logo-panel">
      <div class="brand">
        <span class="brand-mark"></span>
        <span class="brand-name">KAVRO</span>
      </div>
      <div class="brand-sub">CABINETRY INC.</div>
    </div>
    <div class="accent-strip"></div>
    <div class="info-panel contact">
      <p class="contact-name">Marco Delgado</p>
      <p class="contact-role">Owner</p>
      <p class="contact-lines">555-284-7716<br>kavro@mailbox.example<br>www.kavrocabinetry.example</p>
      <p class="contact-address">2290 Harbor Mill rd,<br>Eastbrook, NY, 11900</p>
    </div>
  </section>

  <section class="card-side card-side--back" aria-label="Card back">
    <div class="top-band"></div>
    <div class="logo-panel">
      <div class="brand">
        <span class="brand-mark"></span>
        <span class="brand-name">KAVRO</span>
      </div>
      <div class="brand-sub">CABINETRY INC.</div>
    </div>
    <div class="accent-strip"></div>
    <div class="info-panel">
      <ul class="services">
        <li>CONTEMPORAY KITCHENS</li>
        <li>TRADITIONAL KITCHENS</li>
        <li>VANITIES</li>
        <li>LIBRARIES</li>
        <li>CUSTOM WINE CELLARS</li>
        <li>CUSTOM DESIGN FURNITURE</li>
      </ul>
    </div>
  </section>

</main>
</body>
</html>
```